Professional and creative business card design for recruiting service providers

Our company supports German medium-sized companies in filling vacancies promptly. For this we use social media marketing and bring our customers into the visibility.

We want a professional but also creative design for our business cards.

Please look at lindqvar-staff.de to get an impression of our CI.

Target Market(s)

Small and medium-sized companies in Germany from the industry

Industry/Entity Type

Industrie, Handwerk

Contact Information for Business Card

Name, Position, Telefonnummer, Email, Website

Colors
EE7325
F08F49
F5BC92
FAE3D3
FDF4ED

Requirements
Must have
• A picture of the employee and in the style of www.lindqvar-staff.de

```html
<!DOCTYPE html>
<html lang="en">
<head>
<meta charset="utf-8">
<title>Lindqvar Staff – Business Card</title>
<link rel="stylesheet" href="https://fonts.googleapis.com/css2?family=Montserrat:wght@600;700;800&family=Arimo:wght@400;700&display=swap">
<style>
  :root {
    --orange: #EE7325;
    --orange-deep: #E0601A;
    --orange-mid: #F08F49;
    --orange-soft: #F5BC92;
    --orange-pale: #FAE3D3;
    --cream: #FDF4ED;
    --ink: #141414;
    --white: #FFFFFF;
    --stage: #D9D9D9;
    --photo-dark: #3B3C42;
    --photo-light: #EDEDED;
  }
  * { box-sizing: border-box; margin: 0; padding: 0; }
  html, body {
    width: 1200px; height: 800px; overflow: hidden;
    background: var(--stage);
  }
  .stage {
    position: relative; width: 1200px; height: 800px;
    display: flex; align-items: center; justify-content: center; gap: 40px;
  }
  .card {
    position: relative; width: 530px; height: 303px;
    overflow: hidden;
    box-shadow: 0 14px 30px rgba(0,0,0,0.22);
  }

  /* Front */
  .card-front {
    background: var(--white);
    border-bottom: 4px solid var(--orange);
  }
  .employee-photo {
    position: absolute; right: 0; top: 0; width: 245px; height: 100%;
    background: linear-gradient(180deg, var(--photo-light) 0%, var(--photo-light) 20%, var(--photo-dark) 55%, var(--photo-dark) 100%);
  }
  .brand {
    position: absolute; left: 34px; top: 40px;
    display: flex; align-items: center; gap: 12px;
  }
  .brand-square {
    width: 40px; height: 40px; background: var(--orange);
  }
  .brand-name {
    font-family: "Montserrat", sans-serif; font-weight: 800;
    font-size: 21px; line-height: 1.05; letter-spacing: 1.5px;
    color: var(--ink); text-transform: uppercase;
  }
  .person {
    position: absolute; left: 34px; top: 138px;
  }
  .person-name {
    font-family: "Montserrat", sans-serif; font-weight: 800;
    font-size: 22px; letter-spacing: 1px; color: var(--orange);
    text-transform: uppercase;
  }
  .person-role {
    font-family: "Arimo", sans-serif; font-size: 14px; color: var(--ink);
    margin-top: 2px;
  }
  .contact-list {
    list-style: none; margin-top: 16px;
    font-family: "Arimo", sans-serif; font-size: 14px; color: var(--ink);
  }
  .contact-list li {
    display: flex; align-items: center; gap: 8px; height: 22px;
  }
  .contact-list svg { width: 14px; height: 14px; flex: none; }
  .accent { color: var(--orange); }

  /* Back */
  .card-back { background: var(--orange); }
  .pattern-field {
    position: absolute; inset: 0;
    background: linear-gradient(155deg, var(--orange-mid) 0%, var(--orange) 45%, var(--orange-deep) 100%);
  }
  .back-brand {
    position: absolute; right: 44px; bottom: 58px;
    display: flex; align-items: center; gap: 14px;
    padding: 12px 16px; background: var(--orange);
  }
  .back-brand .brand-square { background: var(--white); width: 36px; height: 36px; }
  .back-brand .brand-name { color: var(--white); font-size: 20px; }
</style>
</head>
<body>
<main class="stage">

  <section class="card card-front" aria-label="Business card front">
    <div class="employee-photo" role="img" aria-label="Portrait photo of the employee in a dark suit and white shirt"></div>

    <div class="brand">
      <span class="brand-square"></span>
      <span class="brand-name">Lindqvar<br>Staff</span>
    </div>

    <div class="person">
      <h1 class="person-name">Mattis Brenner</h1>
      <p class="person-role">Managing Director</p>
      <ul class="contact-list">
        <li>
          <svg viewBox="0 0 24 24" aria-hidden="true"><path fill="var(--orange)" d="M6.6 10.8a15.1 15.1 0 0 0 6.6 6.6l2.2-2.2a1 1 0 0 1 1-.25 11.4 11.4 0 0 0 3.6.57 1 1 0 0 1 1 1V20a1 1 0 0 1-1 1A17 17 0 0 1 3 4a1 1 0 0 1 1-1h3.5a1 1 0 0 1 1 1c0 1.25.2 2.45.57 3.57a1 1 0 0 1-.25 1z"/></svg>
          030-555 018 274
        </li>
        <li>
          <svg viewBox="0 0 24 24" aria-hidden="true"><rect x="2" y="5" width="20" height="14" fill="var(--orange)"/><path d="M2 5l10 8 10-8" fill="none" stroke="var(--white)" stroke-width="2"/></svg>
          info@lindqvar-staff.de
        </li>
        <li>
          <svg viewBox="0 0 24 24" aria-hidden="true"><circle cx="12" cy="12" r="10" fill="var(--orange)"/><path d="M2 12h20M12 2c3 3 3 17 0 20M12 2c-3 3-3 17 0 20" fill="none" stroke="var(--white)" stroke-width="1.4"/></svg>
          <span>www.<span class="accent">lindqvar-staff</span>.de</span>
        </li>
      </ul>
    </div>
  </section>

  <section class="card card-back" aria-label="Business card back">
    <div class="pattern-field" role="img" aria-label="Tonal orange repeating brand pattern"></div>
    <div class="back-brand">
      <span class="brand-square"></span>
      <span class="brand-name">Lindqvar<br>Staff</span>
    </div>
  </section>

</main>
</body>
</html>
```